Coastline Premier Retreats Business Card Design

Design a business card for Coastline Premier Retreats. Look at the website for colors and reference. Card should have logo, name, title, office number, mobile number, email, URL and a tagline like, "Luxury Hotel & Resort Email Marketing" (This might change).

https://www.coastlinepremierretreats.example

The rest I will leave up to your imagination.

Contact Information for Business Card

Logo, name, title, office number, mobile number, email, URL and a tagline like, "Luxury Hotel & Resort Email Marketing" (This might change).

```html
<!DOCTYPE html>
<html lang="en">
<head>
<meta charset="utf-8">
<title>Coastline Premier Retreats – Business Card</title>
<link rel="stylesheet" href="https://fonts.googleapis.com/css2?family=Arimo:wght@400;700&display=swap">
<style>
  :root {
    --backdrop: #141414;
    --card: #1d1d1d;
    --card-back: #1a1a1a;
    --accent: #e8701f;
    --ink: #f2f2f2;
    --ghost: #3b3b3b;
  }
  * { box-sizing: border-box; margin: 0; padding: 0; }
  html, body {
    width: 1200px; height: 1059px; overflow: hidden;
    background: var(--backdrop);
    font-family: "Arimo", Arial, sans-serif;
    color: var(--ink);
  }
  .canvas { position: relative; width: 1200px; height: 1059px; }

  .card { position: absolute; left: 255px; width: 690px; height: 392px; }
  .card--front { top: 89px; background: var(--card); }
  .card--back { top: 547px; background: var(--card-back); }

  .frame { position: absolute; left: 21px; top: 21px; width: 645px; height: 338px; }

  .brand {
    position: absolute; right: 55px; top: 68px;
    display: flex; align-items: center; gap: 10px;
  }
  .brand__mark { width: 12px; height: 12px; background: var(--accent); }
  .brand__name { font-weight: 700; font-size: 19px; letter-spacing: 1px; color: var(--ink); }

  .person { position: absolute; left: 51px; top: 140px; }
  .person__name { font-weight: 700; font-size: 28px; color: var(--accent); letter-spacing: .3px; line-height: 1; }
  .person__title { font-size: 16px; margin-top: 6px; letter-spacing: .3px; }

  .rule { position: absolute; left: 51px; top: 211px; width: 584px; height: 1px; background: var(--accent); }

  .contacts { position: absolute; left: 51px; top: 230px; list-style: none; }
  .contacts li { display: flex; align-items: center; height: 25px; font-size: 16px; }
  .contacts svg { width: 12px; height: 12px; margin-right: 7px; fill: var(--accent); flex: none; }

  .address {
    position: absolute; right: 55px; top: 258px;
    font-size: 16px; text-align: right; line-height: 21px; font-style: normal;
  }

  .tagline {
    position: absolute; left: 0; width: 100%; top: 345px;
    text-align: center; font-size: 17.5px; color: var(--accent);
  }

  .back-name {
    position: absolute; left: 0; width: 100%; top: 176px;
    text-align: center; font-weight: 700; font-size: 34px;
    letter-spacing: 2px; color: var(--ghost);
  }
</style>
</head>
<body>
<main class="canvas">

  <section class="card card--front" aria-label="Business card front">
    <svg class="frame" viewBox="0 0 645 338" aria-hidden="true">
      <path d="M157 337 H1 V1 H644 V337 H490" fill="none" stroke="var(--accent)" stroke-width="2"/>
    </svg>

    <div class="brand">
      <span class="brand__mark"></span>
      <span class="brand__name">COASTLINE PREMIER RETREATS</span>
    </div>

    <div class="person">
      <h1 class="person__name">DANIEL REEVE</h1>
      <p class="person__title">CEO/Founder</p>
    </div>

    <div class="rule"></div>

    <ul class="contacts">
      <li>
        <svg viewBox="0 0 12 12"><path d="M3 0h6a1 1 0 0 1 1 1v10a1 1 0 0 1-1 1H3a1 1 0 0 1-1-1V1a1 1 0 0 1 1-1zm0.3 1.3v8h5.4v-8zM6 9.8a.7.7 0 1 0 0 1.4.7.7 0 0 0 0-1.4z"/></svg>
        555.014.2090
      </li>
      <li>
        <svg viewBox="0 0 12 12"><path d="M0 4c0-2 3-3 6-3s6 1 6 3v1H9V3.6H3V5H0zM2 6h8l1 5H1z"/></svg>
        +34 600 555 014
      </li>
      <li>
        <svg viewBox="0 0 12 12"><path d="M0 5l6-4 6 4v7H0zM1.2 5.6L6 8.6l4.8-3L6 2.5z"/></svg>
        info@coastlinepremierretreats.example
      </li>
      <li>
        <svg viewBox="0 0 12 12"><circle cx="6" cy="6" r="6"/><path d="M3 3.5c1 .3 1.5 1 1.2 2L5.5 7 5 9.5 3.5 8 2 5.5zM7.5 2c1 .5 2 1 2.5 2.5L8.5 5.5 7 4z" fill="var(--card)"/></svg>
        www.coastlinepremierretreats.example
      </li>
    </ul>

    <address class="address">
      Po Box, 48 B Harbor Rd<br>
      North America, AB 40120
    </address>

    <p class="tagline">Luxury Hotel &amp; Resort Email Marketing</p>
  </section>

  <section class="card card--back" aria-label="Business card back">
    <p class="back-name">COASTLINE PREMIER RETREATS</p>
  </section>

</main>
</body>
</html>
```